Stonebrace Business Card Design

The Stonebrace Co is an aggregate (crushing) equipment dealer serving Western Canadian provinces. Stonebrace is a distributor of aggregate equipment for different manufacturers.

We are looking to change and update the existing business card which has been used since the existence of the company. A copy of existing card has been attached for reference. The Stonebrace Co logo we want to remain the same and we want the green color to remain the same.

We are wanting something new with a different look. A refreshing card to show a new modern and updated look. No longer wanting to have the manufacturers on the back of the card but something more like our logo on the back of the card with a statement like "Crushing Solutions"

ideas could be:
- card can be different colors on front and back
- front or reverse of the card could possibly be the green color with the logo in black

Target Market(s)

Owners of Aggregate/Crushing companies

Contact Information for Business Card

see above

Requirements
Must have
• - logo to remain same along with same font within logo
• - green color to remain same
Nice to have
• as noted above under project description
Should not have

```html
<!DOCTYPE html>
<html lang="en">
<head>
<meta charset="utf-8">
<title>Stonebrace Business Card</title>
<link rel="stylesheet" href="https://fonts.googleapis.com/css2?family=Roboto:wght@400;500;700;900&family=Roboto+Condensed:wght@500;700&display=swap">
<style>
  :root {
    --brand-green: #8a8b0c;
    --ink: #231f20;
    --paper: #f4f4f2;
    --text-grey: #555555;
    --rule: #c9c9c6;
    --backdrop: #e6e3de;
  }
  * { box-sizing: border-box; margin: 0; padding: 0; }
  html, body {
    width: 1200px; height: 960px; overflow: hidden;
    background: var(--backdrop);
    font-family: "Roboto", Arial, sans-serif;
  }
  .canvas { position: relative; width: 1200px; height: 960px; }

  .card {
    position: absolute;
    width: 598px; height: 342px;
    border-radius: 22px;
  }

  /* Front: green with wordmark */
  .card-front {
    left: 320px; top: 105px;
    background: var(--brand-green);
  }
  .card-front .wordmark {
    position: absolute; left: 86px; top: 163px;
    display: flex; align-items: center; gap: 16px;
  }
  .card-front .wordmark-dot {
    width: 30px; height: 30px; border-radius: 50%;
    background: var(--ink);
  }
  .card-front .wordmark-name {
    font-weight: 900; font-size: 22px; letter-spacing: 0.2px;
    color: var(--ink);
  }
  .card-front .tagline {
    position: absolute; left: 0; right: 0; top: 295px;
    text-align: center;
    font-weight: 500; font-size: 14.5px; color: var(--ink);
  }

  /* Back: white with contact details */
  .card-back {
    left: 320px; top: 493px;
    background: var(--paper);
  }
  .card-back .brand-block {
    position: absolute; left: 40px; top: 100px; width: 300px;
    display: flex; flex-direction: column; align-items: center; gap: 22px;
  }
  .card-back .brand-dot {
    width: 90px; height: 90px; border-radius: 50%;
    background: var(--brand-green);
  }
  .card-back .brand-name {
    font-weight: 900; font-size: 20.5px; color: var(--ink);
  }
  .card-back .divider {
    position: absolute; left: 342px; top: 72px;
    width: 1px; height: 210px; background: var(--rule);
  }
  .contact {
    position: absolute; left: 371px; top: 74px;
    color: var(--text-grey);
  }
  .contact .person-name {
    font-family: "Roboto Condensed", "Arial Narrow", sans-serif;
    font-weight: 700; font-size: 21px; color: var(--brand-green);
    line-height: 1;
  }
  .contact .person-title {
    font-weight: 500; font-size: 14px; color: var(--ink);
    margin-top: 6px;
  }
  .contact .address {
    font-size: 14px; line-height: 19px; margin-top: 10px;
  }
  .contact .lines {
    list-style: none; margin-top: 12px;
    font-size: 14px; line-height: 19px;
  }
  .contact .lines li { display: flex; align-items: center; gap: 8px; }
  .contact .lines svg { width: 14px; height: 14px; fill: var(--brand-green); flex: none; }
</style>
</head>
<body>
<main class="canvas">

  <section class="card card-front" aria-label="Card front">
    <div class="wordmark">
      <span class="wordmark-dot"></span>
      <span class="wordmark-name">THE STONEBRACE CO.</span>
    </div>
    <p class="tagline">Crushing Solutions</p>
  </section>

  <section class="card card-back" aria-label="Card back">
    <div class="brand-block">
      <span class="brand-dot"></span>
      <span class="brand-name">THE STONEBRACE CO.</span>
    </div>
    <div class="divider"></div>
    <div class="contact">
      <p class="person-name">DALEN MARSH</p>
      <p class="person-title">CEO/FOUNDER</p>
      <p class="address">2210- 48B Avenue<br>Nisku, Alberta T9E 3K1</p>
      <ul class="lines">
        <li>
          <svg viewBox="0 0 16 16" aria-hidden="true"><path d="M3.6 1.5l2.3 2.8-1.2 1.8c.9 2 2.4 3.5 4.4 4.4l1.8-1.2 2.8 2.3-1.6 2.4C7 13.6 2.4 9 1.2 3.1z"/></svg>
          780.555.0142
        </li>
        <li>
          <svg viewBox="0 0 16 16" aria-hidden="true"><path d="M4.5 1h7v14h-7zM6 2.8v9h4v-9zM7.3 12.8h1.4v1.2H7.3z" fill-rule="evenodd"/></svg>
          780.555.0187
        </li>
        <li>
          <svg viewBox="0 0 16 16" aria-hidden="true"><path d="M4 1h8v4H4zM1 6h14v6h-2v3H3v-3H1zM4.5 10v3.5h7V10z" fill-rule="evenodd"/></svg>
          780.555.0163
        </li>
        <li>
          <svg viewBox="0 0 16 16" aria-hidden="true"><path d="M1 4h14v9H1zM2.5 5.2L8 9.2l5.5-4z" fill-rule="evenodd"/></svg>
          dalen@stonebr.com
        </li>
        <li>
          <svg viewBox="0 0 16 16" aria-hidden="true"><circle cx="8" cy="8" r="7"/><path d="M4 5.5h3v3H5zM9 9.5h2.5v2.5H9z" fill="#f4f4f2"/></svg>
          www.stonebrace.ca
        </li>
      </ul>
    </div>
  </section>

</main>
</body>
</html>
```